SaaS Early tech startup business card design

Unique design for experience ecommerce platform company. the business cards will be used by executive members. conformance with color code is required.

```html
<!DOCTYPE html>
<html lang="en">
<head>
<meta charset="utf-8">
<title>Velto Business Card</title>
<link href="https://fonts.googleapis.com/css2?family=Lato:wght@400;900&family=Oswald:wght@500&display=swap" rel="stylesheet">
<style>
  :root {
    --backdrop: #0d0d0e;
    --card: #1a1a1b;
    --teal: #14a7a6;
    --blue: #0f6f96;
    --accent: #1593a8;
    --text: #f2f2f2;
    --rule: #8a8a8a;
  }
  * { margin: 0; padding: 0; box-sizing: border-box; }
  html, body {
    width: 1200px; height: 900px; overflow: hidden;
    background: var(--backdrop);
    font-family: "Lato", sans-serif;
  }
  .canvas {
    position: relative; width: 1200px; height: 900px;
  }
  .card {
    position: absolute; left: 250px; width: 700px; height: 390px;
    background: var(--card);
    box-shadow: 0 10px 30px rgba(0,0,0,.6);
    overflow: hidden;
  }
  .card--front { top: 45px; }
  .card--back { top: 465px; }
  .card__band {
    position: absolute; left: 0; right: 0; bottom: 0; height: 12px;
    background: linear-gradient(to bottom, var(--blue), var(--teal));
  }
  .brand {
    position: absolute; left: 0; right: 0; top: 130px;
    text-align: center;
    font-weight: 900; font-size: 104px; line-height: 1;
    letter-spacing: -2px;
    color: var(--accent);
  }
  .person {
    position: absolute; right: 400px; top: 130px; text-align: right;
  }
  .person__name {
    font-family: "Oswald", sans-serif; font-weight: 500;
    font-size: 34px; line-height: 1; color: var(--teal);
    text-transform: uppercase; letter-spacing: -0.5px;
    white-space: nowrap;
  }
  .person__role {
    margin-top: 6px; font-size: 19px; color: var(--text);
    white-space: nowrap;
  }
  .divider {
    position: absolute; left: 322px; top: 130px;
    width: 1px; height: 92px; background: var(--rule);
  }
  .contacts {
    position: absolute; left: 345px; top: 140px;
    list-style: none;
  }
  .contacts__item {
    display: flex; align-items: center; gap: 10px;
    font-size: 20px; color: var(--text); height: 28px;
    white-space: nowrap;
  }
  .contacts__icon { width: 18px; height: 18px; flex: none; }
  .address {
    position: absolute; left: 95px; top: 292px;
    font-size: 20px; color: var(--text);
    white-space: nowrap;
  }
</style>
</head>
<body>
<main class="canvas">
  <section class="card card--front">
    <div class="brand">velto</div>
    <div class="card__band"></div>
  </section>

  <section class="card card--back">
    <div class="person">
      <div class="person__name">Marcus Hale</div>
      <div class="person__role">Managing Director</div>
    </div>
    <div class="divider"></div>
    <ul class="contacts">
      <li class="contacts__item">
        <svg class="contacts__icon" viewBox="0 0 24 24"><path fill="#14a7a6" d="M6.6 10.8a15.1 15.1 0 006.6 6.6l2.2-2.2a1 1 0 011-.25 11.4 11.4 0 003.6.57 1 1 0 011 1V20a1 1 0 01-1 1A17 17 0 013 4a1 1 0 011-1h3.5a1 1 0 011 1c0 1.25.2 2.45.57 3.57a1 1 0 01-.25 1z"/></svg>
        044-555 019 274
      </li>
      <li class="contacts__item">
        <svg class="contacts__icon" viewBox="0 0 24 24"><rect x="2" y="5" width="20" height="14" fill="#14a7a6"/><path d="M2 5l10 8 10-8" fill="none" stroke="#1a1a1b" stroke-width="2"/></svg>
        hello@veltoshop.com
      </li>
      <li class="contacts__item">
        <svg class="contacts__icon" viewBox="0 0 24 24" fill="none" stroke="#14a7a6" stroke-width="2"><circle cx="12" cy="12" r="9"/><path d="M3 12h18M12 3c3 3 3 15 0 18M12 3c-3 3-3 15 0 18"/></svg>
        www.veltoshop.com
      </li>
    </ul>
    <p class="address">87, Harbor Lane, Eastfield, 30518</p>
    <div class="card__band"></div>
  </section>
</main>
</body>
</html>
```